Bathroom sprayer package design needed - with foil (silver)

I would like to mimic the design of this electric shaver - where there are blues, fade outs gradients, strips of gold, lots of flashy foil (silver)
I'm attaching our existing design to provide some copy (words) and context (dimensions of the box). I will only accept/pick designs that look high end and professional. Feel free to be creative with more interesting and relevant copy.

Industry/Entity Type

Retail

Colors
0555a3

```html
<!DOCTYPE html>
<html lang="en">
<head>
<meta charset="utf-8">
<title>HydraVela Stainless Steel Diaper Sprayer – Box Spine and Front</title>
<link rel="stylesheet" href="https://fonts.googleapis.com/css2?family=Fira+Sans+Condensed:wght@600;700;800&display=swap">
<style>
  :root {
    --stage: #1d5fd8;
    --brand-blue: #0555a3;
    --bright-blue: #2f8fff;
    --deep-blue: #0a2fd0;
    --ink: #050608;
    --white: #ffffff;
    --silver-light: #e4e6e8;
    --silver-mid: #b9bcc0;
    --silver-dark: #8d9196;
    --rule-blue: #1e4fe0;
  }
  * { box-sizing: border-box; margin: 0; padding: 0; }
  html, body {
    width: 1200px; height: 1200px; overflow: hidden;
    background: var(--stage);
    font-family: "Fira Sans Condensed", "Arial Narrow", sans-serif;
  }
  .package {
    position: absolute;
    left: 35px; top: 270px;
    width: 1130px; height: 660px;
    display: flex;
  }

  /* Spine panel */
  .box-spine {
    position: relative;
    width: 170px; height: 100%;
    background: var(--white);
    overflow: hidden;
  }
  .box-spine__stripe {
    position: absolute;
    left: 92px; top: 0;
    width: 48px; height: 100%;
    background: var(--ink);
  }
  .box-spine__brand,
  .box-spine__title {
    position: absolute;
    top: 0; height: 100%;
    writing-mode: vertical-rl;
    transform: rotate(180deg);
    display: flex; align-items: center; justify-content: center;
    white-space: nowrap;
    line-height: 1;
  }
  .box-spine__brand {
    left: 12px; width: 76px;
    gap: 14px;
  }
  .box-spine__brand-dot {
    width: 42px; height: 42px; border-radius: 50%;
    background: var(--bright-blue);
  }
  .box-spine__brand-name {
    color: var(--brand-blue);
    font-weight: 800;
    font-size: 64px;
  }
  .box-spine__title {
    left: 92px; width: 48px;
    color: var(--white);
    font-weight: 800;
    font-size: 27px;
    letter-spacing: 1px;
  }

  /* Front panel */
  .box-front {
    position: relative;
    width: 960px; height: 100%;
    overflow: hidden;
    background: linear-gradient(135deg, var(--silver-light) 0%, var(--silver-mid) 35%, var(--silver-light) 55%, var(--silver-dark) 80%, var(--silver-light) 100%);
  }
  .box-front__panel { position: absolute; inset: 0; width: 100%; height: 100%; }
  .product-visual {
    position: absolute;
    left: 95px; top: 170px;
    width: 390px; height: 470px;
    border-radius: 40% 40% 10% 10%;
    background: radial-gradient(ellipse at 50% 45%, #eef3ff 0%, #9fb4d8 30%, #3d5fb8 60%, rgba(10,47,208,0) 78%);
  }
  .brand {
    position: absolute;
    right: 45px; top: 80px;
    display: flex; align-items: center; gap: 14px;
  }
  .brand__dot {
    width: 62px; height: 62px; border-radius: 50%;
    background: var(--bright-blue);
  }
  .brand__name {
    color: var(--white);
    font-weight: 800;
    font-size: 76px;
    line-height: 1;
  }
  .tagline {
    position: absolute;
    right: 45px; top: 182px;
    color: var(--silver-light);
    font-weight: 700;
    font-size: 31px;
    letter-spacing: 0.5px;
  }
  .features {
    position: absolute;
    left: 565px; top: 388px;
    list-style: none;
    width: 355px;
  }
  .features__item {
    color: var(--white);
    font-weight: 700;
    font-size: 27px;
    line-height: 1;
    padding: 9px 0 8px;
    border-bottom: 3px solid var(--rule-blue);
    margin-bottom: 7px;
    white-space: nowrap;
  }
</style>
</head>
<body>
  <div class="package">
    <aside class="box-spine">
      <div class="box-spine__stripe"></div>
      <div class="box-spine__brand">
        <span class="box-spine__brand-dot"></span>
        <span class="box-spine__brand-name">HydraVela</span>
      </div>
      <p class="box-spine__title">STAINLESS STEEL DIAPER SPRAYER</p>
    </aside>

    <section class="box-front">
      <svg class="box-front__panel" viewBox="0 0 1080 740" preserveAspectRatio="none" aria-hidden="true">
        <defs>
          <radialGradient id="panelGlow" cx="0.28" cy="0.6" r="0.62">
            <stop offset="0" stop-color="#2a6cff"/>
            <stop offset="0.45" stop-color="#0a2fd0"/>
            <stop offset="0.8" stop-color="#050608"/>
            <stop offset="1" stop-color="#050608"/>
          </radialGradient>
        </defs>
        <path d="M 300 0 L 1080 0 L 1080 500 Q 1020 690 700 740 L 0 740 L 0 260 Q 90 40 300 0 Z" fill="url(#panelGlow)"/>
      </svg>

      <div class="product-visual" role="img" aria-label="Photo of a brushed stainless steel hand-held bidet sprayer rising from a splash of water droplets"></div>

      <div class="brand">
        <span class="brand__dot"></span>
        <span class="brand__name">HydraVela</span>
      </div>
      <p class="tagline">STAINLESS STEEL DIAPER SPRAYER</p>

      <ul class="features">
        <li class="features__item">HEAVY DUTY STAINLESS STEEL</li>
        <li class="features__item">STRONG WATER PRESSURE</li>
        <li class="features__item">EASILY INSTALLS IN 5 MINUTES</li>
        <li class="features__item">DUAL USE: BIDET &amp; DIAPER</li>
        <li class="features__item">1 YEAR LIMITED WARRANTY</li>
      </ul>
    </section>
  </div>
</body>
</html>
```